Business Card Design Project

We need a business card for a new technology services company. We develop software and implement software packages for our business customers and although we will begin with just one or two service offerings, our service offerings will expand over time. Our name comes from the an author, KL Barrow, and his "idea" was that opportunity should be based on ability and achievement, not on social status.

We would like to see a design that is standard in its size and shape, but stands apart in its dramatic color contrasts. The card should not use too many colors - the colors used in the background should highlight the brilliant blues of the logo (see attachment) to dramatic effect. The background should not be white.

If necessary, you can change the color of the words "KL Barrow", but not the word "Idea".

Card size should be U.S. standard 2 inches by 3.5 inches and provide for 1/8 inch bleed area on each side.

We need a design for both sides of the business card, one side communicating the company logo and contact information, the other side being purely graphical, incorporating the logo but no other information.

Contact Information Required:
Kate Brook
KateBrook@klbarrowvista.com
614-387-2259

Target Market(s)

Business executives

Industry/Entity Type

Software

Requirements
Must have
• It must have the full company logo on one side, and at least the graphic element of the logo on the other. Either that or the full logo on both.
Nice to have
• It would be nice to have a design that could work without needing two different textures. For example, it would be nice if the entire card could be shiny, not just parts of the card.

It would also be nice if texture is something we could add later.
Should not have
• The card should not use the color green.

```html
<!DOCTYPE html>
<html lang="en">
<head>
<meta charset="utf-8">
<title>KL Barrow Vista – Business Cards</title>
<link rel="stylesheet" href="https://fonts.googleapis.com/css2?family=Inter:wght@300;600&display=swap">
<style>
  :root {
    --page: #e9e6e1;
    --card-dark: #111214;
    --card-mid: #24262a;
    --ink-light: #c9ccd0;
    --ink-white: #f2f4f6;
    --brand-blue: #1ba3e6;
    --rule: #8d9197;
  }
  * { box-sizing: border-box; margin: 0; padding: 0; }
  html, body {
    width: 1200px; height: 720px; overflow: hidden;
    background: var(--page);
    font-family: "Inter", Arial, sans-serif;
  }
  .sheet {
    position: relative; width: 1200px; height: 720px;
  }
  .card {
    position: absolute; top: 205px;
    width: 540px; height: 309px;
    overflow: hidden;
    box-shadow: 0 10px 28px rgba(0,0,0,.25);
  }
  .card--front { left: 40px; }
  .card--back { left: 620px; }
  .card__texture {
    position: absolute; inset: 0;
    background: radial-gradient(ellipse at 60% 40%, var(--card-mid) 0%, var(--card-dark) 75%);
  }
  .rule {
    position: absolute; height: 1.5px; background: var(--rule);
  }
  .brand {
    position: absolute; font-weight: 300; color: var(--ink-light);
    letter-spacing: -1px; white-space: nowrap;
  }
  .brand-dot {
    position: absolute; border-radius: 50%; background: var(--brand-blue);
  }
  .card--front .brand { left: 30px; top: 150px; font-size: 38px; }
  .card--front .brand-dot { left: 328px; top: 160px; width: 30px; height: 30px; }
  .rule--under-brand { left: 0; top: 203px; width: 370px; }
  .rule--name { left: 470px; top: 124px; width: 70px; }
  .contact-name {
    position: absolute; left: 345px; top: 114px;
    font-weight: 600; font-size: 17px; letter-spacing: .5px;
    color: var(--brand-blue); text-transform: uppercase;
  }
  .contact-line {
    position: absolute; display: flex; align-items: center; gap: 7px;
    font-size: 13.5px; font-weight: 300; color: var(--ink-white);
    white-space: nowrap;
  }
  .contact-line svg { width: 12px; height: 12px; flex: none; }
  .contact-line--phone { left: 375px; top: 146px; }
  .contact-line--email { left: 300px; top: 226px; }
  .card--back .brand {
    left: 0; right: 0; top: 122px; text-align: center;
    font-size: 50px;
  }
</style>
</head>
<body>
<main class="sheet">
  <section class="card card--front" aria-label="Business card, front">
    <div class="card__texture" role="img" aria-label="Dark woven carbon texture background"></div>
    <span class="brand-dot"></span>
    <div class="brand">KL Barrow Vista</div>
    <div class="rule rule--under-brand"></div>
    <div class="contact-name">Kate Brook</div>
    <div class="rule rule--name"></div>
    <div class="contact-line contact-line--phone">
      <svg viewBox="0 0 12 12" aria-hidden="true"><circle cx="6" cy="6" r="6" fill="#1ba3e6"/><path d="M4 3.2l1 1.3-.6.8c.4.9 1 1.5 1.9 1.9l.8-.6 1.3 1-.7 1.1C5.6 8.6 3.4 6.4 3 4z" fill="#111214"/></svg>
      <span>614-387-2259</span>
    </div>
    <div class="contact-line contact-line--email">
      <svg viewBox="0 0 12 12" aria-hidden="true"><rect x="0.5" y="2.5" width="11" height="7" rx="1" fill="#1ba3e6"/><path d="M1 3.2l5 3.4 5-3.4" stroke="#111214" stroke-width="1" fill="none"/></svg>
      <span>KateBrook@klbarrowvista.com</span>
    </div>
  </section>

  <section class="card card--back" aria-label="Business card, back">
    <div class="card__texture" role="img" aria-label="Dark woven carbon texture background"></div>
    <div class="brand">KL Barrow Vista</div>
  </section>
</main>
</body>
</html>
```